New Company Logo & Responsive Website Design for Codeworks Heron

Codeworks Heron provides a white labeled, digital lending platform technology solutions to the mortgage industry via a SaaS model. Our target market is Mortgage Companies and Banks who are looking for innovative technology to assist both borrowers and loan originators with the lending process, while automating as much of he process as possible.

Codeworks Heron is our company name, and our modular software offerings Include the following Products:

1) Applicant Heron: A customizable, web based, point-of-sale application for borrowers to complete a loan application, and guide them through the mortgage process.

POS Definition
"A point of sale (POS) is the client-facing software solution that allows borrowers to create a customer portal, apply for a loan online, and seamlessly submit needed documentation."

2) Ledger Heron: A Mortgage Loan Origination System

LOS Definition
"A Mortgage Loan Origination System (LOS) is a platform that takes a completed loan application and facilitates the mortgage transaction from origination to post closing. LOS systems may include document management, pricing and eligibility engines, and compliance tools to decrease risk and increase loan manufacturing quality.

3) Dwelling Heron: A brandable, home search website

The LOS and POS definitions provided above are just for your understanding of what these products are, not to be included word-for-word as website content.

We are looking for designs that are elegant, convey technical competency, simple to navigate, and set us apart from the competition.

We are not set on any particular colors at this point, so feel free to choose the best colors for your particular designs.

Please include company logo, both desktop and mobile designs with a template design for the website sub pages.

Some Examples of Mortgage Technology Websites offering similar products. These are to show the typical content, not designs that we particularly like or dislike.

https://brantiq.example/
https://www.clearvantro.example/
https://www.abodefundbuddy.example/
https://www.debtquokka.example/
https://www.ternixapps.example/products/trail

Please send comments with additional questions.

Thank You For your participation.

Mortgage Companies

```html
<!DOCTYPE html>
<html lang="en">
<head>
<meta charset="utf-8">
<title>Codeworks Heron – Mortgage FinTech</title>
<link rel="stylesheet" href="https://fonts.googleapis.com/css2?family=Ubuntu:wght@400;500;700&family=Roboto:wght@400;500;700&family=Montserrat:wght@500;600&display=swap">
<style>
:root{
  --blue:#0d63e8;
  --blue-deep:#1657ee;
  --blue-sky:#1ea3d6;
  --ink:#2b2b2b;
  --muted:#8a8f98;
  --grey-band:#eef0f4;
  --team-band:#e4eefc;
  --white:#ffffff;
  --navy:#143a7a;
}
*{box-sizing:border-box;margin:0;padding:0}
html,body{width:1200px;height:3504px;overflow:hidden;background:var(--white)}
body{position:relative;font-family:"Roboto",sans-serif;color:var(--ink)}
.abs{position:absolute}

/* hero */
.hero{left:0;top:0;width:1200px;height:664px}
.hero svg.bg{position:absolute;left:0;top:0}
.logo{font-family:"Ubuntu",sans-serif;font-weight:500;font-size:33px;color:var(--white);letter-spacing:.2px}
.nav{left:521px;top:43px;display:flex;gap:34px;font-family:"Ubuntu",sans-serif;font-size:19px;color:var(--white)}
.nav .current{font-weight:700}
.btn-login{left:887px;top:27px;width:120px;height:55px;border:2px solid var(--white);border-radius:28px;color:var(--white);font-family:"Ubuntu",sans-serif;font-weight:500;font-size:17px;display:flex;align-items:center;justify-content:center;gap:8px}
.hero-title{left:109px;top:170px;font-family:"Ubuntu",sans-serif;font-size:45px;line-height:61px;color:var(--white)}
.hero-title b{font-weight:700}
.hero-text{left:111px;top:311px;width:400px;font-family:"Ubuntu",sans-serif;font-size:21px;line-height:36px;color:var(--white)}
.btn-start{left:110px;top:487px;width:164px;height:53px;border:2px solid var(--white);border-radius:27px;background:var(--blue-deep);color:var(--white);font-family:"Ubuntu",sans-serif;font-weight:500;font-size:17px;display:flex;align-items:center;justify-content:center;gap:10px}
.device-art{left:578px;top:195px;width:544px;height:281px;border-radius:10px;background:linear-gradient(135deg,#e9eef6,#c9d3e2 60%,#9aa8bd)}

/* section titles */
.section-title{width:1200px;left:0;text-align:center;font-family:"Roboto",sans-serif;font-weight:500;font-size:50px;color:var(--ink);letter-spacing:.5px}
.section-title span{color:var(--blue);font-weight:700;margin-left:14px}

/* services */
.svc{width:294px;height:348px;top:872px}
.svc-photo{position:absolute;left:0;top:0;width:294px;height:230px}
.svc-card{position:absolute;left:19px;top:130px;width:259px;height:218px;background:var(--white);box-shadow:0 4px 12px rgba(0,0,0,.12)}
.svc-card svg{position:absolute;left:0;top:-28px}
.svc-name{position:absolute;left:24px;top:66px;font-size:17px;font-weight:500;color:#444}
.svc-desc{position:absolute;left:24px;top:98px;width:222px;font-size:15px;line-height:21px;color:var(--muted)}
.svc-more{position:absolute;right:0;bottom:0;width:136px;height:35px;color:var(--white);font-weight:700;font-size:15px;display:flex;align-items:center;justify-content:flex-end;padding-right:12px;background:var(--blue);clip-path:polygon(12% 0,100% 0,100% 100%,0 100%)}

/* blog */
.blog-band{left:0;top:1341px;width:1200px;height:641px;background:var(--grey-band)}
.blog-hero{left:109px;top:1539px;width:476px;height:356px;background:linear-gradient(120deg,#061a45,#0b3d87 50%,#18a2c9)}
.post{background:var(--white);border-bottom:3px solid var(--blue);padding:20px 21px;box-shadow:0 2px 8px rgba(0,0,0,.08)}
.post-date{font-family:"Montserrat",sans-serif;font-weight:500;font-size:13px;letter-spacing:.6px;color:#222}
.post-lead{margin-top:16px;font-size:13px;line-height:20px;color:#222}
.post-body{margin-top:12px;font-size:12.5px;line-height:22px;color:#666}
.post.small{width:235px;height:172px}
.post.feature{left:343px;top:1667px;width:223px;height:206px;border-bottom:none;box-shadow:none;padding:20px 23px}

/* contact */
.field{height:58px;border-radius:29px;background:var(--white);box-shadow:0 3px 8px rgba(0,0,0,.14);border:1px solid #eceef2;padding-left:31px;display:flex;align-items:center;font-family:"Ubuntu",sans-serif;font-size:18px;color:#555}
.btn-submit{left:518px;top:2420px;width:162px;height:51px;border-radius:26px;background:var(--blue);color:var(--white);font-weight:700;font-size:17px;display:flex;align-items:center;justify-content:center;letter-spacing:.5px}

/* team */
.team-band{left:0;top:2543px;width:1200px;height:623px;background:var(--team-band)}
.member{width:260px;text-align:center}
.member-photo{width:152px;height:152px;border-radius:50%;margin:0 auto;background:linear-gradient(180deg,#d9dde3,#8c939e);border:3px solid var(--navy)}
.member-name{margin-top:30px;font-size:17px;font-weight:500;color:#1d1d1d}
.member-role{margin-top:10px;font-size:18px;line-height:28px;color:#444}
.member.active .member-name,.member.active .member-role{color:var(--white)}
.member.active .member-photo{border-color:var(--white)}
.active-card{left:620px;top:2784px;width:251px;height:296px;background:var(--blue);border-radius:4px}
.social{width:44px;height:44px;border:2px solid var(--white);border-radius:50%}
.arrow{width:44px;height:43px;border-radius:5px;display:flex;align-items:center;justify-content:center}

/* footer */
.foot-logo{left:0;width:1200px;top:3224px;text-align:center;font-family:"Ubuntu",sans-serif;font-size:37px;font-weight:500;color:var(--blue)}
.foot-item{font-size:16px;line-height:29px;color:#222}
.foot-item b{font-weight:700}
.foot-rule{left:109px;top:3445px;width:982px;height:1px;background:#e3e5e8}
.copyright{left:0;width:1200px;top:3463px;text-align:center;font-size:17px;color:#222}
</style>
</head>
<body>

<header class="abs hero">
  <svg class="bg" width="1200" height="664" viewBox="0 0 1200 664">
    <defs>
      <linearGradient id="heroGrad" x1="0" y1="0" x2="0" y2="1">
        <stop offset="0" stop-color="#1a57f0"/>
        <stop offset="1" stop-color="#20a6d6"/>
      </linearGradient>
    </defs>
    <path d="M0 0H1200V560Q1200 640 1120 640H80Q0 640 0 560Z" fill="url(#heroGrad)"/>
    <path d="M0 575Q6 660 90 660H1110Q1194 660 1200 575" fill="none" stroke="#1aa3d4" stroke-width="7"/>
  </svg>
  <div class="abs logo" style="left:114px;top:40px">Codeworks Heron</div>
  <nav class="abs nav">
    <span class="current">Home</span><span>Solution</span><span>Price</span><span>Contact</span>
  </nav>
  <div class="abs btn-login">Login <svg width="10" height="10" viewBox="0 0 10 10"><path d="M2 1l5 4-5 4" fill="none" stroke="#fff" stroke-width="2"/></svg></div>
  <h1 class="abs hero-title"><b>Mortgage FinTech</b><br>Startup.</h1>
  <p class="abs hero-text">Codeworks Heron is a Fin-Tech Startup that provides a white labeled, digital lending platform technology solutions to the mortgage industry via a SaaS model.</p>
  <div class="abs btn-start">Get Started <svg width="10" height="10" viewBox="0 0 10 10"><path d="M2 1l5 4-5 4" fill="none" stroke="#fff" stroke-width="2"/></svg></div>
  <div class="abs device-art" role="img" aria-label="Laptop, desktop monitor and tablet showing the lending platform dashboards"></div>
</header>

<h2 class="abs section-title" style="top:756px">OUR<span>SERVICES</span></h2>

<article class="abs svc" style="left:137px">
  <div class="svc-photo" role="img" aria-label="Photo of a hand touching digital technology icons" style="background:linear-gradient(135deg,#2a4d6b,#6a9fc0 55%,#d8a86a)"></div>
  <div class="svc-card">
    <svg width="259" height="40" viewBox="0 0 259 40"><path d="M0 40L259 0V40Z" fill="#fff"/><path d="M0 40L259 0" stroke="#1aa3d4" stroke-width="4"/></svg>
    <div class="svc-name">Applicant Heron</div>
    <div class="svc-desc">A customizable, web based, point-of-sale application for borrowers to complete a loan</div>
    <div class="svc-more">LEARN MORE</div>
  </div>
</article>

<article class="abs svc" style="left:456px">
  <div class="svc-photo" role="img" aria-label="Photo of a laptop with glowing data screens" style="background:linear-gradient(135deg,#0b1524,#3a4e6a 50%,#b0405a)"></div>
  <div class="svc-card">
    <svg width="259" height="40" viewBox="0 0 259 40"><path d="M0 40L259 0V40Z" fill="#fff"/><path d="M0 40L259 0" stroke="#1aa3d4" stroke-width="4"/></svg>
    <div class="svc-name">Ledger Heron</div>
    <div class="svc-desc">"A Mortgage Loan Origination System (LOS) is a platform that takes a completed loan</div>
    <div class="svc-more">LEARN MORE</div>
  </div>
</article>

<article class="abs svc" style="left:774px">
  <div class="svc-photo" role="img" aria-label="Photo of a developer working at monitors" style="background:linear-gradient(135deg,#0d2338,#2c5578 55%,#6b8aa6)"></div>
  <div class="svc-card">
    <svg width="259" height="40" viewBox="0 0 259 40"><path d="M0 40L259 0V40Z" fill="#fff"/><path d="M0 40L259 0" stroke="#1aa3d4" stroke-width="4"/></svg>
    <div class="svc-name">Dwelling Heron</div>
    <div class="svc-desc">&nbsp;A brandable, home search website</div>
    <div class="svc-more">LEARN MORE</div>
  </div>
</article>

<section class="abs blog-band"></section>
<h2 class="abs section-title" style="top:1399px">OUR<span>BLOG</span></h2>

<div class="abs blog-hero" role="img" aria-label="Photo of program code on a blue screen"></div>
<article class="abs post feature">
  <div class="post-date">JUNE 01 2022</div>
  <div class="post-lead">Ut enim ad minima venia, quis nostrum exercitation</div>
  <div class="post-body">Ut enim ad minima venia, quis nostrum exercitation ut enimd minima veniam, quis nostrum exercitation.</div>
</article>

<article class="abs post small" style="left:604px;top:1539px">
  <div class="post-date">JUNE 01 2022</div>
  <div class="post-lead">Ut enim ad minima venia, quis</div>
  <div class="post-body">Ut enim ad minima venia, quis nostrum exercitation ut enimd minima veniam.</div>
</article>
<article class="abs post small" style="left:852px;top:1539px">
  <div class="post-date">JUNE 01 2022</div>
  <div class="post-lead">Ut enim ad minima venia, quis</div>
  <div class="post-body">Ut enim ad minima venia, quis nostrum exercitation ut enimd minima veniam.</div>
</article>
<article class="abs post small" style="left:604px;top:1722px">
  <div class="post-date">JUNE 01 2022</div>
  <div class="post-lead">Ut enim ad minima venia, quis</div>
  <div class="post-body">Ut enim ad minima venia, quis nostrum exercitation ut enimd minima veniam.</div>
</article>
<article class="abs post small" style="left:852px;top:1722px">
  <div class="post-date">JUNE 01 2022</div>
  <div class="post-lead">Ut enim ad minima venia, quis</div>
  <div class="post-body">Ut enim ad minima venia, quis nostrum exercitation ut enimd minima veniam.</div>
</article>

<h2 class="abs section-title" style="top:2045px">CONTACT<span>US</span></h2>
<div class="abs field" style="left:229px;top:2151px;width:359px">First Name</div>
<div class="abs field" style="left:609px;top:2151px;width:361px">Last Name</div>
<div class="abs field" style="left:229px;top:2231px;width:359px">Email</div>
<div class="abs field" style="left:609px;top:2231px;width:361px">Comapy</div>
<div class="abs field" style="left:229px;top:2316px;width:741px">Subject</div>
<div class="abs btn-submit">SUBMIT</div>

<section class="abs team-band"></section>
<h2 class="abs section-title" style="top:2605px">OUR<span>TEAM</span></h2>
<div class="abs active-card"></div>

<div class="abs member" style="left:82px;top:2720px">
  <div class="member-photo" role="img" aria-label="Portrait photo of team member"></div>
  <div class="member-name">MARCUS ELLWOOD</div>
  <div class="member-role">CEO &amp; IT Consultant</div>
</div>
<div class="abs member" style="left:345px;top:2720px">
  <div class="member-photo" role="img" aria-label="Portrait photo of team member"></div>
  <div class="member-name">DORIAN VALE</div>
  <div class="member-role">Database &amp; Logistics<br>Consulting</div>
</div>
<div class="abs member active" style="left:616px;top:2720px">
  <div class="member-photo" role="img" aria-label="Portrait photo of team member"></div>
  <div class="member-name">TOBIAS RENNICK</div>
  <div class="member-role">Pascalite apps &amp; Social<br>Media</div>
</div>
<div class="abs social" style="left:697px;top:3007px"></div>
<div class="abs social" style="left:751px;top:3007px"></div>
<div class="abs member" style="left:881px;top:2720px">
  <div class="member-photo" role="img" aria-label="Portrait photo of team member"></div>
  <div class="member-name">LEANDER CORVI</div>
  <div class="member-role">Devops &amp; Jovra<br>development</div>
</div>

<div class="abs arrow" style="left:33px;top:2884px;background:var(--white)"><svg width="12" height="14" viewBox="0 0 12 14"><path d="M8 2L3 7l5 5" fill="none" stroke="#333" stroke-width="2"/></svg></div>
<div class="abs arrow" style="left:1122px;top:2884px;background:var(--navy)"><svg width="12" height="14" viewBox="0 0 12 14"><path d="M4 2l5 5-5 5" fill="none" stroke="#fff" stroke-width="2"/></svg></div>

<footer>
  <div class="abs foot-logo">Codeworks Heron</div>

  <svg class="abs" style="left:106px;top:3305px" width="36" height="46" viewBox="0 0 36 46"><path d="M18 44C18 44 3 26 3 17a15 15 0 0 1 30 0c0 9-15 27-15 27z" fill="none" stroke="#1a7ee8" stroke-width="2.5"/><circle cx="18" cy="17" r="6" fill="none" stroke="#1a7ee8" stroke-width="2.5"/></svg>
  <div class="abs foot-item" style="left:163px;top:3319px">Address:<br><b>Codeworks Heron</b><br><b>dummy text here</b></div>

  <svg class="abs" style="left:499px;top:3320px" width="32" height="32" viewBox="0 0 24 24"><path d="M6.6 10.8a15.1 15.1 0 0 0 6.6 6.6l2.2-2.2a1 1 0 0 1 1-.25 11.4 11.4 0 0 0 3.6.57 1 1 0 0 1 1 1V20a1 1 0 0 1-1 1A17 17 0 0 1 3 4a1 1 0 0 1 1-1h3.5a1 1 0 0 1 1 1c0 1.25.2 2.45.57 3.6a1 1 0 0 1-.25 1z" fill="#1a7ee8"/></svg>
  <div class="abs foot-item" style="left:556px;top:3319px">Call Now:<br><b>+1-555-014-2290</b></div>

  <svg class="abs" style="left:828px;top:3322px" width="36" height="26" viewBox="0 0 36 26"><rect x="0" y="0" width="36" height="26" rx="2" fill="#1a7ee8"/><path d="M1 2l17 13L35 2" fill="none" stroke="#fff" stroke-width="2"/></svg>
  <div class="abs foot-item" style="left:886px;top:3319px">Mail Now:<br><b>info@codeworksheron.example</b></div>

  <div class="abs foot-rule"></div>
  <div class="abs copyright">2022 Codeworks Heron. All Rights Reserved.</div>
</footer>

</body>
</html>
```